Web Design

We need a website for a company based in Doha Qatar called
Lumara Maid Service.

It is the number one maid cleaning service company, and we have branches all over qatar.

Luxury Cleaning Service Provider.

The color scheme is gold, yellow and black like the logo.

Before they get to the website, there is an intro video.

The website should depict luxury.

Target Market(s)

People who need maids at their houses.

Industry/Entity Type

Cleaning Service

Requirements
Must have
• Luxury, Sleek, Modern

The opening sequence is a video which I already have. Its too big to upload here so I am going to put it on youtube.

After the opening sequence, the home page should have a widescreen photo background and it should change every five seconds, the first background photo should be of qatar westbay skyline. Then the second background should be of maid photos in cleaning positions. Then the third background should be of cleaner photos etc.

We will send you all the tabs and all the content later.

```html
<!DOCTYPE html>
<html lang="en">
<head>
<meta charset="utf-8">
<title>Lumara Maid Service</title>
<link rel="stylesheet" href="https://fonts.googleapis.com/css2?family=Jost:wght@300;400;500;700&display=swap">
<style>
  :root {
    --gold: #ffd400;
    --white: #ffffff;
    --light: #dcdcdc;
    --black: #000000;
    --card: #1b1b1b;
    --rule: #3a3a3a;
    --header: rgba(30, 36, 50, 0.78);
  }
  * { box-sizing: border-box; margin: 0; padding: 0; }
  html, body { width: 1200px; height: 1082px; overflow: hidden; background: var(--black); }
  body { font-family: "Jost", sans-serif; position: relative; color: var(--white); }

  .hero-photo {
    position: absolute; left: 0; top: 0; width: 1200px; height: 884px;
    background:
      linear-gradient(180deg, rgba(20,28,48,0.55) 0%, rgba(20,24,34,0.35) 45%, rgba(10,12,16,0.6) 100%),
      linear-gradient(180deg, #3d5376 0%, #59688a 30%, #6f6f70 55%, #4b4843 75%, #2a2a2a 100%);
  }

  .site-header {
    position: absolute; left: 0; top: 0; width: 1200px; height: 108px;
    background: var(--header);
    border-top: 2px solid #4a5670;
  }
  .brand {
    position: absolute; left: 136px; top: 38px;
    display: flex; align-items: center; gap: 10px;
    font-weight: 500; font-size: 20px; color: var(--gold); letter-spacing: 0.5px;
  }
  .brand-dot { width: 22px; height: 22px; border-radius: 50%; background: var(--gold); }
  .main-nav { position: absolute; top: 44px; left: 0; width: 1200px; }
  .main-nav a {
    position: absolute; font-size: 15px; font-weight: 400; color: var(--light);
    text-decoration: none; text-transform: uppercase; white-space: nowrap;
  }
  .main-nav a.active { color: var(--gold); }

  .hero-text { position: absolute; left: 0; width: 1200px; text-align: center; text-transform: uppercase; }
  .hero-title { top: 268px; font-size: 70px; font-weight: 300; color: var(--light); letter-spacing: -0.5px; }
  .hero-title strong { color: var(--gold); font-weight: 700; }
  .hero-sub { top: 366px; font-size: 42px; font-weight: 700; color: var(--white); }
  .hero-tag { top: 428px; font-size: 31px; font-weight: 300; color: var(--white); }

  .more-btn {
    position: absolute; left: 412px; top: 506px; width: 377px; height: 80px;
    border: 2px solid var(--white); display: flex; align-items: center; justify-content: center;
    font-size: 33px; font-weight: 700; color: var(--gold); text-transform: uppercase; text-decoration: none;
  }

  .slide-arrow { position: absolute; top: 358px; width: 30px; height: 46px; }
  .slide-arrow.prev { left: 20px; }
  .slide-arrow.next { left: 1148px; }

  .service { position: absolute; top: 723px; width: 291px; height: 249px; background: var(--card); }
  .service-photo { height: 161px; }
  .service-name {
    padding: 13px 0 0 19px; font-size: 33px; line-height: 35px; text-transform: uppercase; color: var(--gold);
  }
  .service-name b { font-weight: 700; display: block; }
  .service-name span { font-weight: 300; display: block; }

  .footer-rule { position: absolute; left: 131px; top: 1005px; width: 938px; height: 1px; background: var(--rule); }
  .copyright {
    position: absolute; left: 131px; top: 1035px; font-size: 12px; color: var(--light);
    text-transform: uppercase; letter-spacing: -0.2px;
  }
  .social { position: absolute; left: 942px; top: 1028px; display: flex; gap: 7px; }
  .social span { width: 27px; height: 27px; border-radius: 50%; border: 1.5px solid #666; display: block; }
  .social span.active { border-color: var(--gold); border-width: 2px; }
</style>
</head>
<body>
  <div class="hero-photo" role="img" aria-label="Wide photo of a city waterfront skyline with towers, a marina and moored boats"></div>

  <header class="site-header">
    <div class="brand"><span class="brand-dot"></span>Lumara Maid Service</div>
    <nav class="main-nav">
      <a class="active" style="left:472px">Home</a>
      <a style="left:564px">About us</a>
      <a style="left:679px">Services</a>
      <a style="left:786px">Our staff</a>
      <a style="left:911px">Blog</a>
      <a style="left:996px">Contacts</a>
    </nav>
  </header>

  <svg class="slide-arrow prev" viewBox="0 0 30 46"><polyline points="24,4 7,23 24,42" fill="none" stroke="#e6e6e6" stroke-width="6"/></svg>
  <svg class="slide-arrow next" viewBox="0 0 30 46"><polyline points="6,4 23,23 6,42" fill="none" stroke="#e6e6e6" stroke-width="6"/></svg>

  <h1 class="hero-text hero-title"><strong>Lumara</strong> Maid Service</h1>
  <p class="hero-text hero-sub">Lorem ipsum dolor sit amet</p>
  <p class="hero-text hero-tag">Consectetur adipisicin</p>
  <a class="more-btn">More information</a>

  <section class="service" style="left:131px">
    <div class="service-photo" role="img" aria-label="Gloved hands cleaning a window" style="background:linear-gradient(135deg,#c98a6a 0%,#8fb6d8 45%,#e8eef2 100%)"></div>
    <h2 class="service-name"><b>Window</b><span>Cleaning</span></h2>
  </section>
  <section class="service" style="left:455px">
    <div class="service-photo" role="img" aria-label="Worker pressure washing a wooden deck in front of a house" style="background:linear-gradient(180deg,#d8dde2 0%,#9aa3aa 55%,#8a7a66 100%)"></div>
    <h2 class="service-name"><b>Pressure</b><span>Cleaning</span></h2>
  </section>
  <section class="service" style="left:777px">
    <div class="service-photo" role="img" aria-label="Cleaner washing a glass facade" style="background:linear-gradient(135deg,#b08a70 0%,#e2e6e8 45%,#c8d4da 100%)"></div>
    <h2 class="service-name"><b>Eco</b><span>Cleaning</span></h2>
  </section>

  <div class="footer-rule"></div>
  <p class="copyright">Lumara Maid Service © 2014 All rights are reserved &nbsp;Privacy policy</p>
  <div class="social">
    <span></span><span class="active"></span><span></span><span></span>
  </div>
</body>
</html>
```